Design a Cover for a Book on Innovation

I need a design for my book: The Quiet Harvest of Invention
It is about the following:

Innovation is not just for those endowed with special talent or skills in technology. This book describes the thought framework that consists of seven principal differences between the current period and the past. Innovation is happening along these shifts. Understanding the differences can allow for consistent innovation and the identification of real opportunities.
Updates

To All: All of you show great talent as designers. I've added a bit more to the description. Feel free to ask questions. Best, DT

Font styles to use
Sans Serif

Colors

Designer to choose colors to be used in the design.

Requirements
Must have
• It should feel modern and innovative. It should incorporate the meaning of Quiet Harvest.
Nice to have
• It should have the title, and a holder spot for the subtitle and author's name Dara Tovens
Should not have
• It should not be overly busy. Sleek modern design that still gets the point across. Alternatively an image that is a full cover graphic.

```html
<!DOCTYPE html>
<html lang="en">
<head>
<meta charset="utf-8">
<title>The Quiet Harvest of Invention — Book Cover</title>
<link rel="stylesheet" href="https://fonts.googleapis.com/css2?family=Inter:ital,wght@0,200;0,300;0,700;1,200;1,300&display=swap">
<style>
  :root {
    --cover-yellow-top: #ddb800;
    --cover-yellow-mid: #e3bf00;
    --cover-yellow-bottom: #e8c900;
    --bulb-shadow: rgba(60, 48, 10, 0.20);
    --bulb-glow: rgba(255, 246, 190, 0.45);
    --ink: #262318;
    --ink-soft: #3a3420;
  }
  html, body {
    margin: 0;
    padding: 0;
    width: 927px;
    height: 1200px;
    overflow: hidden;
  }
  .cover {
    position: relative;
    width: 927px;
    height: 1200px;
    overflow: hidden;
    font-family: "Inter", "Helvetica Neue", Arial, sans-serif;
    color: var(--ink);
    background: linear-gradient(180deg, var(--cover-yellow-top) 0%, var(--cover-yellow-mid) 55%, var(--cover-yellow-bottom) 100%);
  }
  .bulb-photo {
    position: absolute;
    left: 250px;
    top: 0;
    width: 480px;
    height: 850px;
    border-radius: 0 0 240px 240px;
    background:
      radial-gradient(ellipse 60% 22% at 50% 30%, var(--bulb-glow) 0%, rgba(255, 246, 190, 0) 100%),
      linear-gradient(180deg, rgba(60, 48, 10, 0.05) 0%, var(--bulb-shadow) 35%, rgba(60, 48, 10, 0.10) 80%, rgba(60, 48, 10, 0) 100%);
  }
  .title {
    position: absolute;
    right: 464px;
    top: 428px;
    margin: 0;
    text-align: right;
    font-weight: 200;
    font-size: 51px;
    line-height: 47px;
    letter-spacing: -1.8px;
    color: var(--ink);
  }
  .title span { display: block; }
  .subtitle {
    position: absolute;
    left: 0;
    right: 0;
    top: 963px;
    margin: 0;
    text-align: center;
    font-style: italic;
    font-weight: 200;
    font-size: 25px;
    letter-spacing: -0.4px;
    text-transform: uppercase;
    color: var(--ink-soft);
  }
  .author {
    position: absolute;
    left: 0;
    right: 0;
    top: 1071px;
    margin: 0;
    text-align: center;
    font-weight: 700;
    font-size: 19.5px;
    letter-spacing: 0.3px;
    text-transform: uppercase;
    color: var(--ink);
  }
</style>
</head>
<body>
  <main class="cover">
    <div class="bulb-photo" role="img" aria-label="Photograph of clear light bulbs with black sockets hanging at different heights on long black cords, one bulb hanging lowest below the title"></div>
    <h1 class="title">
      <span>The</span>
      <span>Quiet</span>
      <span>Harvest</span>
      <span>of</span>
      <span>Invention.</span>
    </h1>
    <p class="subtitle">Differences between current period and past</p>
    <p class="author">Dara Tovens</p>
  </main>
</body>
</html>
```